Need Help having my business card stand out

I am the owner of Birchway Canine Training and would like for my business cards to stand out. I have been trying to keep designing them myself but I can't get what I have in my head on the card. I will try my best to post templates that I like for inspirations. I want something unique but elegant. I don't want in to look cartoony or cheesy. It needs to pop in a pet shop but also in a coffee shop or gym.

Target Market(s)

Dog owners, Married ,No young kids Jr High school kids and up (maybe kids on the way) Executives, Stay at home moms/wives, Small business owners

Industry/Entity Type

Dog Training

Contact Information for Business Card

Lowell Spratt, 281-904-3376, info@birchwaycanine.example, www.birchwaycanine.example

Colors

Designer to choose colors to be used in the design.

Requirements
Must have
• my logo
Should not have
• Cursive lettering

```html
<!DOCTYPE html>
<html lang="en">
<head>
<meta charset="utf-8">
<title>Birchway Canine Training – Business Card</title>
<link href="https://fonts.googleapis.com/css2?family=Montserrat:wght@400;800&family=Josefin+Sans:wght@300&family=Open+Sans:wght@400;700&display=swap" rel="stylesheet">
<style>
  :root {
    --backdrop: #4a90df;
    --card-base: #22508c;
    --card-deep: #1b4278;
    --wedge-light: #2f7fd3;
    --wedge-dark: #1d4d8c;
    --band: #0e2350;
    --badge: #2d7fd1;
    --logo-ink: #0f2452;
    --rule: #2f7fd3;
    --text-light: #ffffff;
    --text-soft: #a9c8ee;
  }
  * { box-sizing: border-box; margin: 0; padding: 0; }
  html, body { width: 1200px; height: 900px; overflow: hidden; }
  body {
    background: var(--backdrop);
    font-family: "Open Sans", sans-serif;
    position: relative;
  }
  .card {
    position: absolute;
    left: 250px;
    width: 700px;
    height: 400px;
    overflow: hidden;
    background: radial-gradient(ellipse at 40% 40%, var(--card-base), var(--card-deep));
    box-shadow: 0 10px 24px rgba(10, 30, 70, 0.35);
  }
  .card--front { top: 40px; }
  .card--back { top: 460px; }
  .card__wedges { position: absolute; inset: 0; width: 100%; height: 100%; }

  .front__band {
    position: absolute;
    left: 175px; top: 0;
    width: 68px; height: 200px;
    background: var(--band);
    border-radius: 0 0 6px 6px;
  }
  .front__badge {
    position: absolute;
    left: 181px; top: 134px;
    width: 56px; height: 56px;
    border-radius: 50%;
    background: var(--badge);
    border: 3px solid var(--band);
  }

  .brand {
    position: absolute;
    display: flex;
    align-items: center;
    gap: 12px;
  }
  .brand__dot {
    width: 34px; height: 34px;
    border-radius: 50%;
    background: var(--logo-ink);
    flex: none;
  }
  .brand__name {
    font-family: "Open Sans", sans-serif;
    font-weight: 700;
    color: var(--logo-ink);
    line-height: 1.1;
  }
  .front__brand { left: 350px; top: 100px; width: 300px; }
  .front__brand .brand__name { font-size: 34px; }
  .front__rule {
    position: absolute;
    top: 225px;
    height: 2px;
    background: var(--rule);
  }
  .front__rule--left { left: 260px; width: 80px; }
  .front__rule--right { left: 610px; width: 80px; }

  .back__brand { left: 450px; top: 160px; width: 220px; }
  .back__brand .brand__name { font-size: 28px; }

  .contact { position: absolute; left: 90px; top: 70px; color: var(--text-light); }
  .contact__name {
    font-family: "Montserrat", sans-serif;
    font-size: 26px;
    font-weight: 400;
  }
  .contact__name strong { font-weight: 800; }
  .contact__role {
    font-family: "Josefin Sans", sans-serif;
    font-weight: 300;
    font-size: 17px;
    font-variant: small-caps;
    letter-spacing: 0.5px;
    color: var(--text-soft);
    margin-top: 4px;
  }
  .contact__list { list-style: none; margin-top: 10px; }
  .contact__item {
    display: flex;
    align-items: center;
    gap: 10px;
    font-size: 14px;
    height: 39px;
  }
  .contact__icon {
    width: 20px; height: 20px;
    background: var(--wedge-light);
    flex: none;
  }
</style>
</head>
<body>

<section class="card card--front" aria-label="Card front">
  <svg class="card__wedges" viewBox="0 0 700 400" preserveAspectRatio="none" aria-hidden="true">
    <defs>
      <linearGradient id="wedgeTop" x1="1" y1="0" x2="0" y2="0">
        <stop offset="0" stop-color="#2f7fd3"/><stop offset="1" stop-color="#1d4d8c" stop-opacity="0"/>
      </linearGradient>
      <linearGradient id="wedgeBottom" x1="0" y1="0" x2="1" y2="0">
        <stop offset="0" stop-color="#2f7fd3"/><stop offset="1" stop-color="#1d4d8c" stop-opacity="0.2"/>
      </linearGradient>
    </defs>
    <polygon points="420,0 700,0 700,55" fill="url(#wedgeTop)"/>
    <polygon points="0,235 0,400 390,400" fill="url(#wedgeBottom)"/>
  </svg>
  <div class="front__band"></div>
  <div class="front__badge"></div>
  <div class="brand front__brand">
    <span class="brand__dot"></span>
    <span class="brand__name">Birchway Canine Training</span>
  </div>
  <div class="front__rule front__rule--left"></div>
  <div class="front__rule front__rule--right"></div>
</section>

<section class="card card--back" aria-label="Card back">
  <svg class="card__wedges" viewBox="0 0 700 400" preserveAspectRatio="none" aria-hidden="true">
    <polygon points="420,0 700,0 700,70" fill="url(#wedgeTop)"/>
    <polygon points="0,290 0,400 440,400" fill="url(#wedgeBottom)"/>
  </svg>

  <div class="contact">
    <h1 class="contact__name"><strong>Lowell</strong> Spratt</h1>
    <p class="contact__role">Designation</p>
    <ul class="contact__list">
      <li class="contact__item">
        <svg class="contact__icon" viewBox="0 0 20 20" aria-hidden="true"><path d="M10 3a5 5 0 0 0-5 5c0 4 5 9 5 9s5-5 5-9a5 5 0 0 0-5-5zm0 7a2 2 0 1 1 0-4 2 2 0 0 1 0 4z" fill="#0e2350"/></svg>
        <span>000 Alder Lane, Suite 300, Fairview, US 0000</span>
      </li>
      <li class="contact__item">
        <svg class="contact__icon" viewBox="0 0 20 20" aria-hidden="true"><path d="M4 7c0-2 3-3 6-3s6 1 6 3v1h-3V7H7v1H4zM6 9h8l2 6H4z" fill="#0e2350"/></svg>
        <span>281-904-3376</span>
      </li>
      <li class="contact__item">
        <svg class="contact__icon" viewBox="0 0 20 20" aria-hidden="true"><rect x="3" y="5" width="14" height="10" fill="#0e2350"/><path d="M3 5l7 6 7-6" stroke="#2f7fd3" stroke-width="1.5" fill="none"/></svg>
        <span>info@birchwaycanine.example</span>
      </li>
      <li class="contact__item">
        <svg class="contact__icon" viewBox="0 0 20 20" aria-hidden="true"><circle cx="10" cy="10" r="6.5" fill="none" stroke="#0e2350" stroke-width="1.6"/><path d="M3.5 10h13M10 3.5c-3 3.5-3 9.5 0 13M10 3.5c3 3.5 3 9.5 0 13" stroke="#0e2350" stroke-width="1.2" fill="none"/></svg>
        <span>www.birchwaycanine.example</span>
      </li>
    </ul>
  </div>

  <div class="brand back__brand">
    <span class="brand__dot"></span>
    <span class="brand__name">Birchway Canine Training</span>
  </div>
</section>

</body>
</html>
```